Velora Entertainment

Logo for business card design

Target Market(s)

potential film investors and screenwriters

Industry/Entity Type

Business

Contact Information for Business Card

as shown, website here is a placeholder position

Requirements
Must have
• great visual appeal
Nice to have
• harmony of colors; must evoke spirit of
• U.S.-China cooperation

```html
<!DOCTYPE html>
<html lang="en">
<head>
<meta charset="utf-8">
<title>Velora Entertainment – Business Card</title>
<link rel="stylesheet" href="https://fonts.googleapis.com/css2?family=Source+Sans+3:wght@400;600;700&display=swap">
<style>
  :root {
    --page-bg: #dcdcdc;
    --card-bg: #eef0f2;
    --panel-bg: #c3c6cc;
    --text-dark: #2e2f33;
    --accent-red: #d3262b;
    --bar-navy: #1c1f6e;
    --bar-gold: #e8ae12;
    --bar-red: #c9242a;
    --rule: #55575c;
  }
  * { margin: 0; padding: 0; box-sizing: border-box; }
  html, body {
    width: 1200px;
    height: 969px;
    overflow: hidden;
    background: var(--page-bg);
    font-family: "Source Sans 3", sans-serif;
  }
  .card {
    position: absolute;
    left: 100px;
    top: 200px;
    width: 1000px;
    height: 568px;
    background: var(--card-bg);
    box-shadow: 0 10px 30px rgba(0,0,0,0.18);
    overflow: hidden;
  }
  .contact-panel {
    position: absolute;
    left: 0; top: 0;
    width: 445px;
    height: 100%;
    background: var(--panel-bg);
    color: var(--text-dark);
    font-size: 27px;
    line-height: 1;
  }
  .contact-panel .line {
    position: absolute;
    left: 58px;
    white-space: nowrap;
  }
  .person-name {
    color: var(--accent-red);
    font-size: 34px;
    font-weight: 600;
  }
  .divider {
    position: absolute;
    left: 58px;
    width: 270px;
    border-top: 2px dotted var(--rule);
  }
  .label {
    color: var(--accent-red);
    font-weight: 700;
  }
  .color-bar {
    position: absolute;
    left: 445px;
    top: 0;
    width: 5px;
    height: 100%;
    display: flex;
    flex-direction: column;
  }
  .color-bar span { flex: 1; }
  .color-bar .navy { background: var(--bar-navy); }
  .color-bar .gold { background: var(--bar-gold); }
  .color-bar .red { background: var(--bar-red); }
  .brand {
    position: absolute;
    left: 450px;
    right: 0;
    top: 250px;
    display: flex;
    align-items: center;
    justify-content: center;
    gap: 16px;
  }
  .brand-square {
    width: 40px;
    height: 40px;
    background: var(--bar-red);
  }
  .brand-name {
    font-size: 44px;
    font-weight: 700;
    color: var(--text-dark);
    white-space: nowrap;
  }
</style>
</head>
<body>
  <div class="card">
    <div class="contact-panel">
      <div class="line person-name" style="top:48px">Daniel Hart</div>
      <div class="line" style="top:95px">CEO/Founder</div>
      <div class="line" style="top:133px">daniel@veloraent.com</div>
      <div class="divider" style="top:200px"></div>
      <div class="line" style="top:228px">2140 Larchmont Road</div>
      <div class="line" style="top:265px">Fairbrook, Oregon 97210</div>
      <div class="line" style="top:302px">www.veloraent.com</div>
      <div class="divider" style="top:373px"></div>
      <div class="line" style="top:403px"><span class="label">P :</span> 555 214 7730</div>
      <div class="line" style="top:440px"><span class="label">F :</span> 555 214 7731</div>
      <div class="line" style="top:477px"><span class="label">M :</span> 555 214 7732</div>
    </div>
    <div class="color-bar">
      <span class="navy"></span>
      <span class="gold"></span>
      <span class="red"></span>
    </div>
    <div class="brand">
      <span class="brand-square"></span>
      <span class="brand-name">Velora Entertainment</span>
    </div>
  </div>
</body>
</html>
```